KBT Business Cards

We require business cards for our business. We would like a matte black back to the card, with our logo centred in the middle. The front side of the card is open to design.

Target Market(s)

Clients looking for legal services (professional)

Industry/Entity Type

Legal

Contact Information for Business Card

Doran Kelbrath
Partner
Mobile: 0461 738 524
Email: doran@kbtlaw.co
Website: www.kbtlaw.co
Level 3, 118 Wendmore Street
Sydney NSW 2000

Font styles to use
Other font styles liked:
• Avenir

Colors
f04a50
ffffff
1b1b1b

Requirements
Must have
• Black back with logo included in the centre of the card.
• Our font is Avenir.

```html
<!DOCTYPE html>
<html lang="en">
<head>
<meta charset="utf-8">
<title>KBT Law — Business Cards</title>
<link href="https://fonts.googleapis.com/css2?family=Nunito+Sans:wght@400;600;700;800&display=swap" rel="stylesheet">
<style>
  :root {
    --brand-red: #d4234c;
    --ink: #1b1b1b;
    --matte-black: #1b1b1b;
    --matte-black-soft: #262626;
    --paper: #ffffff;
    --stage: #2a2a2c;
    --muted: #3a3a3a;
  }
  * { box-sizing: border-box; margin: 0; padding: 0; }
  html, body { width: 1200px; height: 880px; overflow: hidden; }
  body {
    background: var(--stage);
    font-family: "Nunito Sans", "Avenir", sans-serif;
    position: relative;
  }
  .card {
    position: absolute;
    width: 560px;
    height: 320px;
    border-radius: 18px;
    overflow: hidden;
  }

  /* Back side: matte black with centred name */
  .card-back {
    left: 60px; top: 70px;
    background: linear-gradient(160deg, var(--matte-black-soft) 0%, var(--matte-black) 100%);
    box-shadow: 0 0 0 1px rgba(255,255,255,0.06);
    display: flex; align-items: center; justify-content: center;
  }
  .wordmark {
    display: flex; align-items: center; gap: 18px;
    font-weight: 800; letter-spacing: 2px; text-transform: uppercase;
    white-space: nowrap;
  }
  .wordmark-square { width: 46px; height: 46px; flex: none; }
  .card-back .wordmark { color: var(--paper); font-size: 44px; }
  .card-back .wordmark-square { background: var(--brand-red); }

  /* Front side */
  .card-front {
    left: 580px; top: 490px;
    background: var(--paper);
    color: var(--ink);
  }
  .card-front .wordmark {
    position: absolute; left: 40px; top: 44px;
    color: var(--ink); font-size: 38px;
  }
  .card-front .wordmark-square { width: 40px; height: 40px; background: var(--brand-red); }

  .person { position: absolute; left: 40px; top: 146px; width: 250px; }
  .person-name {
    color: var(--brand-red); font-weight: 800; font-size: 19px;
    text-transform: uppercase; letter-spacing: 0.5px; line-height: 1.1;
  }
  .person-title { font-size: 15px; font-weight: 600; color: var(--muted); }
  .person-rule { height: 2px; background: var(--brand-red); margin: 8px 0 10px; }
  .contact-list { list-style: none; font-size: 15px; }
  .contact-list li { display: flex; align-items: center; gap: 10px; line-height: 1.5; }
  .contact-icon { width: 14px; height: 14px; flex: none; }

  .divider { position: absolute; left: 300px; right: 34px; top: 168px; height: 1.5px; background: var(--brand-red); }
  .address {
    position: absolute; right: 34px; top: 176px;
    text-align: right; font-size: 14px; font-weight: 600; line-height: 1.45;
    font-style: normal;
  }

  .card-footer { position: absolute; left: 0; bottom: 0; width: 560px; height: 62px; display: block; }
  .website {
    position: absolute; right: 34px; bottom: 17px;
    color: var(--paper); font-size: 14px; letter-spacing: 4px; font-weight: 600;
  }
</style>
</head>
<body>
  <section class="card card-back" aria-label="Card back">
    <div class="wordmark"><span class="wordmark-square"></span><span>KBT Law</span></div>
  </section>

  <section class="card card-front" aria-label="Card front">
    <div class="wordmark"><span class="wordmark-square"></span><span>KBT Law</span></div>

    <div class="person">
      <p class="person-name">Doran Kelbrath</p>
      <p class="person-title">Partner</p>
      <div class="person-rule"></div>
      <ul class="contact-list">
        <li>
          <svg class="contact-icon" viewBox="0 0 14 14" aria-hidden="true"><rect x="1.5" y="1.5" width="11" height="11" fill="none" stroke="var(--brand-red)" stroke-width="2"/></svg>
          0461 738 524
        </li>
        <li>
          <svg class="contact-icon" viewBox="0 0 14 14" aria-hidden="true"><rect x="1" y="3" width="12" height="9" fill="var(--brand-red)"/><path d="M1 3 L7 8 L13 3" fill="none" stroke="var(--paper)" stroke-width="1.4"/></svg>
          doran@kbtlaw.co
        </li>
      </ul>
    </div>

    <div class="divider"></div>
    <address class="address">
      Level 3, 118 Wendmore Street<br>Sydney NSW 2000
    </address>

    <svg class="card-footer" viewBox="0 0 560 62" aria-hidden="true">
      <!-- thin red base line across the full width -->
      <rect x="0" y="54" width="560" height="8" fill="var(--brand-red)"/>
      <!-- black stripe running along the left, rising into the step -->
      <path d="M0 40 L300 40 Q308 40 312 34 L318 24 L318 32 Q312 48 300 48 L0 48 Z" fill="var(--ink)"/>
      <!-- raised red panel holding the web address -->
      <path d="M338 6 L560 6 L560 62 L312 62 L312 54 L316 54 Q322 54 324 46 L326 18 Q328 6 338 6 Z" fill="var(--brand-red)"/>
    </svg>
    <span class="website">www.kbtlaw.co</span>
  </section>
</body>
</html>
```